Dental Medical History Form - Content provided

Design a medical history form for a dental practice. Content is provided so all that is needed is the formatting to make it look great and easy to read.

"Patient Information" to include all information contained in top portion of the "Patient Medical History Form" docx file.

"Medical History" should follow the formatting and content of the "Exact Medical History" file as this is what the entry fields look like in our practice software and so we would like it to match.

1st page - Patient info, allergies, medications, antibiotics, joint replacement, pregnancy.

2nd page - Do you have, or have you had, any of the following? . . . . . . .
Updates

Target Market(s)

All ages but must be clear enough for elderly to read. Use as much space as possible to keep font size bigger yet keep to two pages

Industry/Entity Type

Dental

Font styles to use
Sans Serif

Requirements
Must have
• All content provided
• Our logo at the top (file provided)
• Century Gothic Font
• Limit to two pages

```html
<!DOCTYPE html>
<html lang="en">
<head>
<meta charset="utf-8">
<title>Harbourline Dental – Confidential Medical History</title>
<link rel="stylesheet" href="https://fonts.googleapis.com/css2?family=Didact+Gothic&family=PT+Sans+Narrow:wght@400;700&display=swap">
<style>
:root{
  --bg:#e9e8e6;
  --paper:#ffffff;
  --ink:#5e4d42;
  --ink-soft:#8a7a70;
  --rule:#9c8b80;
  --band:#e4ddd8;
  --band-edge:#cfc4bc;
}
*{box-sizing:border-box;margin:0;padding:0}
html,body{width:1200px;height:784px;overflow:hidden;background:var(--bg)}
body{font-family:"PT Sans Narrow",sans-serif;color:var(--ink);position:relative}
.form-page{
  position:absolute;left:316px;top:18px;width:568px;height:748px;
  background:var(--paper);box-shadow:0 2px 6px rgba(0,0,0,.12);
  padding:18px 26px 16px;display:flex;flex-direction:column;
}
.form-header{display:flex;justify-content:space-between;align-items:flex-start}
.brand{display:flex;align-items:center;gap:8px;font-family:"Didact Gothic",sans-serif;font-size:26px;color:var(--ink-soft);letter-spacing:.5px}
.brand-dot{width:11px;height:11px;border:1.5px solid var(--ink-soft)}
.practice-address{text-align:right;font-size:9px;font-weight:700;line-height:1.3}
.form-title{font-family:"Didact Gothic",sans-serif;font-size:20px;letter-spacing:2px;text-align:center;margin:8px 0 10px;}
.form-title span{border-bottom:2px solid var(--ink);padding-bottom:1px}
.section{padding:9px 0 8px;border-top:6px solid var(--band);box-shadow:inset 0 1px 0 var(--band-edge)}
.section:first-of-type{border-top:none;box-shadow:none;padding-top:2px}
.section-title{font-size:10.5px;font-weight:700;text-align:center;margin-bottom:5px}
.q{font-size:10.5px;font-weight:700;margin-bottom:5px}
.row{display:flex;align-items:center;gap:6px;margin-bottom:6px;font-size:10px;color:var(--ink-soft)}
.row label{white-space:nowrap}
.field{flex:1;height:15px;border:1px solid var(--rule)}
.field.short{flex:0 0 70px}
.sub{position:relative}
.sub-caption{font-size:9px;color:var(--ink-soft);position:absolute;top:-11px;left:40%}
.check{display:inline-block;width:10px;height:10px;border:1px solid var(--rule);vertical-align:middle;margin:0 4px 0 3px}
.opts{display:flex;flex-wrap:wrap;gap:4px 12px;font-size:10px;color:var(--ink);margin-bottom:6px}
.lines{display:grid;grid-template-columns:1fr 1fr;gap:0 22px}
.line{height:17px;border-bottom:1px solid var(--rule)}
.yn{display:grid;grid-template-columns:190px auto;row-gap:6px;font-size:10px}
.turn-tab{align-self:flex-start;margin-top:auto;background:var(--band);border:1px solid var(--band-edge);font-size:10px;font-weight:700;padding:3px 12px}
</style>
</head>
<body>
<main class="form-page">
  <header class="form-header">
    <div class="brand"><span class="brand-dot"></span>harbourline dental</div>
    <div class="practice-address">Harbourline Dental . Suite 4/18 Marlow Street,<br>Kelso NSW 2795<br>(02) 55 310 482</div>
  </header>
  <h1 class="form-title"><span>CONFIDENTIAL MEDICAL HISTORY</span></h1>

  <section class="section patient-details">
    <div class="row sub"><label>Name:</label><div class="field sub"><span class="sub-caption">First</span></div><div class="field sub"><span class="sub-caption">Last</span></div></div>
    <div class="row"><label>Address:</label><div class="field"></div><label>Email Address:</label><div class="field"></div></div>
    <div class="row"><label>DOB:</label><div class="field"></div></div>
    <div class="row"><label>Phone Number(s): Mobile</label><div class="field"></div><label>Work</label><div class="field"></div><label>Home</label><div class="field"></div></div>
    <div class="row"><label>Emergency Contact Person: Name</label><div class="field"></div><label>Relationship</label><div class="field"></div><label>Phone number</label><div class="field"></div></div>
  </section>

  <section class="section general-info">
    <h2 class="section-title">General Information</h2>
    <div class="row"><label>Practice Name:</label><div class="field"></div><label>Address:</label><div class="field"></div><label>Phone:</label><div class="field"></div></div>
    <div class="row"><label>Do you have dental health fund cover?</label><label>Yes<span class="check"></span>or<span class="check"></span>No</label><label>If so, what is the name of the fund?</label><div class="field"></div></div>
    <div class="row"><label>Fund Number?</label><div class="field"></div><label>Priority Number on card: 0<span class="check"></span>1<span class="check"></span>2<span class="check"></span>3<span class="check"></span>4<span class="check"></span>5</label></div>
    <div class="row"><label>Occupation:</label><div class="field"></div><label>Referred by:</label><div class="field"></div></div>
  </section>

  <section class="section allergies">
    <p class="q">Please indicate if you are allergic to any of the following?</p>
    <div class="opts"><span>Aspirin<span class="check"></span></span><span>Codeine<span class="check"></span></span><span>Penicillin<span class="check"></span></span><span>Sulfites<span class="check"></span></span><span>Latex<span class="check"></span></span><span>Local Anaesthetic<span class="check"></span></span><span>Lactose<span class="check"></span></span><span>Nickel<span class="check"></span></span></div>
    <div class="row"><label>Other:</label><div class="field"></div></div>
  </section>

  <section class="section medications">
    <p class="q">Are you currently taking, or have ever taken, any of the following medication?</p>
    <div class="opts"><span>Asthma inhaler<span class="check"></span></span><span>Anti-epileptics<span class="check"></span></span><span>Anti-depressants<span class="check"></span></span><span>Blood Pressure<span class="check"></span></span><span>Blood Thinners<span class="check"></span></span><span>Bisphosphonates<span class="check"></span></span></div>
    <div class="opts"><span>Chemotherapy<span class="check"></span></span><span>Insulin<span class="check"></span></span><span>Immunosuppressants<span class="check"></span></span><span>Steroids<span class="check"></span></span><span>Oral Contraceptive<span class="check"></span></span><span>Other<span class="check"></span></span></div>
    <p class="q">Please specify medication name, dose, and frequency where possible:</p>
    <div class="lines"><div class="line"></div><div class="line"></div><div class="line"></div><div class="line"></div><div class="line"></div><div class="line"></div></div>
  </section>

  <section class="section conditions">
    <div class="yn">
      <span>Do you require antibiotic cover?</span><span>Yes<span class="check"></span>No<span class="check"></span></span>
      <span>Have you had a joint replacement?</span><span>Yes<span class="check"></span>No<span class="check"></span></span>
      <span>Women: Are you pregnant?</span><span>Yes<span class="check"></span>No<span class="check"></span>Possible<span class="check"></span>How Many Weeks?<span class="check"></span><span class="check" style="margin-left:0"></span></span>
    </div>
  </section>

  <div class="turn-tab">Please Turn Over</div>
</main>
</body>
</html>
```